To design a brand identity that is simple and creative with 'Corvane' as the brand name, I like modern simple fonts like helvetica neue, I want to print both sides of the card, I am open to dark front and white back, but the design needs to transfer well to letter heads and email signatures, I am looking for sophisticated and elegant, but open minded about clever and off the wall, I do not do 'boring' Corvane Ventures is the mother company for a small group, specialising in Management & consulting, Software development and construction, we have a high level of integrity, we are transparent and accountable for what we do. my images are provided as a guide only, Im not expecting them to be just copied, Im looking for a creator and passionate thinker, who will put life into their work.

Target Market(s)

usually business minded people who are looking for something different in me, such as leadership, confidence and focus with thinking that is per haps a little outside the box..

Industry/Entity Type

Construction

Requirements
Must have
• clean, minmalistic
Nice to have
• custom logo
Should not have
• boring, traditional

```html
<!DOCTYPE html>
<html lang="en">
<head>
<meta charset="utf-8">
<title>Corvane Ventures – Business Card</title>
<link rel="stylesheet" href="https://fonts.googleapis.com/css2?family=Open+Sans:ital,wght@0,300;0,400;0,600;1,400&display=swap">
<style>
  :root {
    --backdrop: #e4e4e8;
    --card-dark: #1e1e1e;
    --card-dark-edge: #2c2c2c;
    --card-light: #ffffff;
    --brand-orange: #f0561e;
    --coral: #ef5a4e;
    --gold: #f5a800;
    --ink-light: #f2f2f2;
    --ink-dark: #2a2a2a;
    --muted: #7c7c7c;
    --rule: #9a9a9a;
  }
  * { margin: 0; padding: 0; box-sizing: border-box; }
  html, body {
    width: 1200px; height: 987px; overflow: hidden;
    background: var(--backdrop);
    font-family: "Open Sans", "Helvetica Neue", Arial, sans-serif;
  }
  .stage {
    width: 1200px; height: 987px;
    display: flex; flex-direction: column; align-items: center; justify-content: center;
    gap: 56px;
  }
  .card {
    position: relative;
    width: 700px; height: 400px;
    border-radius: 34px;
    overflow: hidden;
    box-shadow: 0 10px 28px rgba(0,0,0,.18);
  }

  /* Front – dark side */
  .card--front {
    background: linear-gradient(160deg, var(--card-dark-edge) 0%, var(--card-dark) 55%, #141414 100%);
    color: var(--ink-light);
  }
  .card--front .texture {
    position: absolute; inset: 0;
    background: linear-gradient(115deg, rgba(255,255,255,.05), rgba(255,255,255,0) 60%);
  }
  .brand-lockup {
    position: absolute; left: 250px; top: 52px;
    display: flex; align-items: center; gap: 22px;
  }
  .brand-dot {
    width: 58px; height: 58px; border-radius: 50%;
    background: var(--brand-orange);
  }
  .brand-name {
    font-weight: 300; font-size: 76px; line-height: 1;
    color: var(--brand-orange); letter-spacing: 1px;
  }
  .tagline {
    position: absolute; left: 330px; top: 150px;
    font-style: italic; font-size: 17px; color: var(--muted);
  }
  .divider {
    position: absolute; left: 60px; right: 60px; top: 196px;
    height: 2px;
    background: linear-gradient(90deg, rgba(154,154,154,0), var(--rule) 20%, #d8d8d8 50%, var(--rule) 80%, rgba(154,154,154,0));
  }
  .holder {
    position: absolute; left: 330px; top: 220px;
    font-size: 24px;
  }
  .holder .name { color: var(--gold); font-weight: 600; }
  .holder .title { color: var(--ink-light); font-weight: 400; }
  .contact {
    position: absolute; left: 60px; top: 278px;
    list-style: none; font-size: 19px; line-height: 1.75;
  }
  .contact li { display: flex; align-items: center; gap: 10px; }
  .contact .icon { width: 18px; height: 18px; flex: none; }
  .contact .spacer { width: 18px; flex: none; }

  /* Back – light side */
  .card--back { background: var(--card-light); }
  .back-wordmark {
    position: absolute; right: 62px; top: 54px;
    font-weight: 300; font-size: 132px; line-height: 1;
    color: var(--brand-orange); letter-spacing: 2px;
  }
  .services {
    position: absolute; left: 62px; top: 232px;
    list-style: none; display: flex; flex-wrap: wrap; gap: 6px 26px;
    width: 560px;
    font-size: 20px; color: var(--coral);
  }
  .services li::before {
    content: "•"; color: var(--muted); margin-right: 6px;
  }
  .website {
    position: absolute; left: 62px; top: 320px;
    font-size: 22px; letter-spacing: 6px; color: var(--ink-dark);
  }
</style>
</head>
<body>
<main class="stage">

  <section class="card card--front" aria-label="Card front">
    <div class="texture"></div>
    <div class="brand-lockup">
      <span class="brand-dot"></span>
      <span class="brand-name">Corvane</span>
    </div>
    <p class="tagline">…in the creation business.</p>
    <div class="divider"></div>
    <p class="holder"><span class="name">Your Name,</span> <span class="title">Title</span></p>
    <ul class="contact">
      <li>
        <svg class="icon" viewBox="0 0 18 18" aria-hidden="true">
          <circle cx="9" cy="9" r="8.5" fill="var(--gold)"/>
          <path d="M6 4.5c-.8.4-1.3 1.2-1 2.3.7 2.6 3 5.1 5.6 6 1 .3 1.9-.1 2.3-.9l-1.6-1.4-1.1.7c-1.2-.6-2.2-1.6-2.8-2.8l.7-1.1z" fill="#1e1e1e"/>
        </svg>
        <span>+61 0400 552 017</span>
      </li>
      <li><span class="spacer"></span><span>Po Box 512 Parth 6031</span></li>
      <li>
        <svg class="icon" viewBox="0 0 18 18" aria-hidden="true">
          <rect x="0.5" y="2.5" width="17" height="13" rx="2" fill="var(--gold)"/>
          <path d="M2.5 5l6.5 5 6.5-5" fill="none" stroke="#1e1e1e" stroke-width="1.6"/>
        </svg>
        <span>names@corvane.ventures</span>
      </li>
    </ul>
  </section>

  <section class="card card--back" aria-label="Card back">
    <p class="back-wordmark">Corvane.</p>
    <ul class="services">
      <li>Management &amp; Consulting</li>
      <li>Software Development</li>
      <li>Construction</li>
    </ul>
    <p class="website">www.corvane.com</p>
  </section>

</main>
</body>
</html>
```